Web Design Project

We are an IT System Integrator. We provide Korvin 450 ERP System, CRM etc. We also provide hardware, networking servicing. Please look at www.zolvantix.com.sg. They provide the same service as us. We like to redesign our web site. I will attached the color that I prefer for reference.

Our website is www.tadurk.com.sg.  It has been created about 14 years ago.  We are trying to revamp it with a new look and information.   The new website must be informative, fast.    I have attached an attachment which show the color that I prefer(brownish golden).   

Our competitor (www.zolvantix.com) is carrying the same trade as us.  They have all the informations In their website that we will like to have.  Therefore I recommend you to take a look at my competitor website and have a better   
understanding on the kind of information I would like to have for my new website.

This project is guarantee to the person with the best design.  We can have it guarantee.

Target Market(s)

Corporate and companies

Industry/Entity Type

Hardware

```html
<!DOCTYPE html>
<html lang="en">
<head>
<meta charset="utf-8">
<title>Tadurk Information Systems Pte Ltd</title>
<link href="https://fonts.googleapis.com/css2?family=Roboto:wght@400;500;700&family=PT+Sans+Narrow:wght@700&family=Montserrat:wght@600&display=swap" rel="stylesheet">
<style>
:root{
  --gold:#b8782c;
  --gold-light:#e0a84c;
  --gold-deep:#9a5f1c;
  --ink:#1c1c1c;
  --text:#333;
  --nav:#141414;
  --panel:#ececec;
  --footer:#3a3a3a;
  --footer-dark:#2a2a2a;
  --line:#c9c9c9;
}
*{box-sizing:border-box;margin:0;padding:0}
html,body{width:1190px;height:1200px;overflow:hidden}
body{position:relative;font-family:"Roboto",Arial,sans-serif;color:var(--text);
  background:linear-gradient(#f6f6f6 0,#eaeaea 380px,#dcdcdc 382px,#f8f8f8 480px,#fff 700px,#fff 1030px)}
.abs{position:absolute}
.top-strip{left:0;top:0;width:1190px;height:8px;background:var(--gold)}
.util-tab{left:656px;top:0;width:298px;height:24px;background:var(--gold);border-radius:0 0 10px 10px;
  display:flex;justify-content:center;align-items:center;gap:6px;font-size:10px;color:#fff}
.util-tab span.sep{opacity:.8}
.brand{left:256px;top:34px;display:flex;align-items:center;gap:10px}
.brand .mark{width:46px;height:46px;border-radius:50%;background:var(--gold)}
.brand .name{font-family:"Roboto",sans-serif;font-weight:700;font-size:11px;line-height:21px;color:var(--gold);letter-spacing:.3px}
.phones{right:244px;top:82px;text-align:right;font-size:16px;color:#444}
.phones b{font-size:20px;color:var(--gold);font-weight:700}
.phones .row{display:flex;align-items:center;justify-content:flex-end;gap:6px;height:26px}
.nav{left:226px;top:136px;width:744px;height:45px;background:var(--nav);border-radius:3px 3px 0 0;display:flex;align-items:center}
.nav a{color:#fff;font-size:12px;font-weight:700;text-decoration:none;height:45px;display:flex;align-items:center;padding:0 17px;border-right:1px solid #333}
.nav a.active{background:var(--gold);color:#fff}
.search{margin-left:auto;margin-right:6px;width:132px;height:27px;background:#fff;border-radius:2px;display:flex;align-items:center;justify-content:space-between;padding:0 6px;font-size:10px;color:#555}
.hero{left:226px;top:181px;width:744px;height:261px;background:linear-gradient(90deg,#fafafa,#fff 60%,#f4f4f4);overflow:hidden}
.hero-art{left:24px;top:2px;width:300px;height:236px;border-radius:40% 40% 10px 10px;background:radial-gradient(circle at 50% 40%,#8a8a8a 0,#777 30%,#c48a3e 55%,rgba(200,140,60,.0) 75%)}
.hero h1{left:347px;top:10px;font-family:"Montserrat",sans-serif;font-weight:600;font-size:21px;letter-spacing:2.5px;line-height:27px;color:var(--ink);white-space:nowrap}
.hero p{left:347px;top:72px;width:325px;font-family:"PT Sans Narrow",sans-serif;font-weight:700;font-size:14px;line-height:21px;color:#111}
.hero .cta{left:346px;top:150px;width:150px;height:30px;border-radius:15px;background:linear-gradient(#c98a38,#a86a20);color:#fff;font-weight:700;font-size:13px;display:flex;align-items:center;justify-content:center}
.arrow-btn{width:22px;height:34px;background:#fff;display:flex;align-items:center;justify-content:center;box-shadow:0 0 3px rgba(0,0,0,.2)}
.welcome{left:252px;top:474px;width:692px;height:44px;border-bottom:1px dotted #999;display:flex;align-items:center;gap:10px}
.welcome .dot{width:22px;height:30px;border-radius:50%;background:var(--gold)}
.welcome h2{font-size:18px;font-weight:400;color:var(--gold)}
.welcome h2 strong{color:var(--ink);font-weight:700;font-size:19px}
.intro{left:252px;top:532px;width:700px;font-size:8.8px;line-height:14.4px;color:#222;text-align:justify}
.card{top:650px;width:218px;height:232px;background:var(--panel);border:1px solid #bbb;box-shadow:inset 0 0 0 3px #fff}
.card .photo{position:absolute;left:9px;top:9px;width:200px;height:90px}
.card h3{position:absolute;left:14px;top:112px;font-size:14px;font-weight:400;color:var(--ink)}
.card h3 span{color:var(--gold)}
.card ul{position:absolute;left:16px;top:141px;list-style:none;font-size:9.5px;line-height:15px;color:#222}
.card li::before{content:"»";margin-right:5px;font-weight:700}
.card .more{position:absolute;right:13px;bottom:11px;font-size:9.5px;color:#222}
.card .more span{color:var(--gold)}
.quick{left:726px;top:650px;width:218px;height:232px;background:var(--panel);border:1px solid #bbb;box-shadow:inset 0 0 0 3px #fff;padding:10px 11px}
.quick h3{text-align:center;font-size:16px;font-weight:500;color:var(--ink);margin-bottom:6px;letter-spacing:-.3px}
.quick h3 span{color:var(--gold)}
.field{height:19px;background:#fff;border:1px solid #c4c4c4;margin-bottom:3.5px;font-size:8.5px;color:#777;padding:4px 8px;display:flex;justify-content:space-between}
.field.area{height:51px}
.btns{display:flex;gap:6px;margin-top:5px}
.btn{height:19px;background:#fff;border:1px solid #c4c4c4;display:flex;align-items:center;font-size:11px;color:#222;padding-left:6px;gap:8px}
.btn i{width:22px;height:17px;background:var(--gold);display:flex;align-items:center;justify-content:center}
.btn.clear{color:#999}
.partners{left:250px;top:922px;width:693px;height:78px;background:linear-gradient(#fbfbfb,#e4e4e4);border:1px solid #ccc;border-radius:3px;display:flex;align-items:center;justify-content:space-around;padding:0 34px}
.partner{font-weight:700;font-size:19px;color:#1a1a1a;letter-spacing:-.3px}
.partner.blue{color:#1c4f96}
.slide{width:20px;height:20px;background:#9a9a9a;border-radius:2px;display:flex;align-items:center;justify-content:center}
.footer{left:0;top:1034px;width:1190px;height:138px;background:linear-gradient(var(--footer-dark),var(--footer))}
.footer h4{position:absolute;font-size:10.5px;font-weight:700;color:var(--gold-light)}
.flinks{position:absolute;list-style:none;font-size:8.5px;color:#ddd}
.flinks li{width:80px;height:15px;border-bottom:1px dotted #777;padding-left:12px;position:relative;line-height:14px}
.flinks li::before{content:"»";position:absolute;left:1px;color:#aaa}
.vline{position:absolute;top:30px;height:88px;border-left:1px dotted #777}
.social{position:absolute;left:644px;font-size:12px;font-weight:700;color:#ccc;display:flex;align-items:center;gap:8px}
.social i{width:16px;height:16px;background:#3d7bb8;border-radius:2px}
.fbrand{position:absolute;left:778px;top:26px;display:flex;align-items:center;gap:8px}
.fbrand .mark{width:36px;height:36px;border-radius:50%;background:#888}
.fbrand .name{font-size:8px;line-height:14px;font-weight:700;color:var(--gold)}
.subscribe{position:absolute;left:780px;top:78px;font-size:13px;font-weight:700;color:#ccc}
.sub-row{position:absolute;left:779px;top:98px;display:flex;gap:5px}
.sub-row .in{width:105px;height:15px;background:#fff;border-radius:2px;font-size:8.5px;color:#999;padding:2px 5px}
.sub-row .go{width:44px;height:13px;margin-top:1px;background:var(--gold);border-radius:3px;font-size:7.5px;color:#fff;text-align:center;line-height:13px}
.copyright{left:0;top:1172px;width:1190px;height:28px;background:var(--gold);color:#fff;font-size:10px;display:flex;align-items:center;justify-content:center}
</style>
</head>
<body>
<div class="abs top-strip"></div>
<nav class="abs util-tab">
  <span>Home</span><span class="sep">|</span><span>Log Incident</span><span class="sep">|</span><span>Enquiry</span><span class="sep">|</span><span>Contact</span><span class="sep">|</span><span>Client Support</span>
</nav>

<header>
  <div class="abs brand"><div class="mark"></div><div class="name">TADURK<br>INFORMATION<br>SYSTEMS PTE LTD</div></div>
  <div class="abs phones">
    <div class="row">
      <svg width="16" height="16" viewBox="0 0 24 24"><path d="M6.6 10.8a15 15 0 0 0 6.6 6.6l2.2-2.2c.3-.3.7-.4 1-.2 1.1.4 2.3.6 3.6.6.6 0 1 .4 1 1V20c0 .6-.4 1-1 1A17 17 0 0 1 3 4c0-.6.4-1 1-1h3.5c.6 0 1 .4 1 1 0 1.3.2 2.5.6 3.6.1.3 0 .7-.2 1z" fill="var(--gold)"/></svg>
      Phone #: <b>(065) 6100-2740</b></div>
    <div class="row">Toll Free Phone#: <b>012.555.0148</b></div>
  </div>
</header>

<nav class="abs nav">
  <a class="active">COMPANY</a><a>PRODUCTS</a><a>LEDGRA</a><a>SERVICES</a><a>CLIENTELE</a><a>CAREERS</a><a style="border:0">INFOBIN</a>
  <div class="search">Search here
    <svg width="18" height="18" viewBox="0 0 24 24"><circle cx="9" cy="9" r="6" fill="none" stroke="var(--gold)" stroke-width="2.5"/><path d="M13.5 13.5l7 7" stroke="var(--gold)" stroke-width="3" stroke-linecap="round"/></svg>
  </div>
</nav>

<section class="abs hero">
  <svg class="abs" style="left:0;top:0" width="744" height="261" viewBox="0 0 744 261">
    <defs><linearGradient id="swoosh" x1="0" x2="1"><stop offset="0" stop-color="#a86a20"/><stop offset=".6" stop-color="#c8892f"/><stop offset=".85" stop-color="#f0c850"/><stop offset="1" stop-color="#c88a30"/></linearGradient></defs>
    <path d="M0 220 C200 260 420 250 560 170 C640 130 700 140 744 140 L744 261 L0 261Z" fill="url(#swoosh)"/>
    <path d="M0 215 C220 250 420 240 560 160 C640 120 700 130 744 132" fill="none" stroke="#2b2b2b" stroke-width="6"/>
    <path d="M0 238 C200 258 360 250 470 225" fill="none" stroke="#444" stroke-width="2"/>
  </svg>
  <div class="abs hero-art" role="img" aria-label="Illustration of figures assembling a round puzzle"></div>
  <h1 class="abs">TADURK INFORMATION<br>SYSTEMS PTE LTD</h1>
  <p class="abs">For more than 20 years, LEDGRA has provided reliable software solutions optimized to take advantage of new technologies and meet the unique requirements of companies.</p>
  <div class="abs cta">Click to Read More</div>
</section>
<div class="abs arrow-btn" style="left:222px;top:286px"><svg width="10" height="14"><path d="M8 1L2 7l6 6" fill="none" stroke="#111" stroke-width="2.5"/></svg></div>
<div class="abs arrow-btn" style="left:951px;top:286px"><svg width="10" height="14"><path d="M2 1l6 6-6 6" fill="none" stroke="#111" stroke-width="2.5"/></svg></div>

<section>
  <div class="abs welcome"><div class="dot"></div><h2>Welcome to <strong>TADURK INFORMATION</strong> SYSTEMS</h2></div>
  <p class="abs intro">Lorem ipsum dolor sit amet, consectetuer adipiscing elit, sed diam nonummy nibh euismod tincidunt ut laoreet dolore magna aliquam erat volutpat. Ut wisi enim ad minim veniam, quis nostrud exerci tation ullamcorper suscipit lobortis nisl ut aliquip ex ea commodo consequat. Duis autem vel eum iriure dolor in hendrerit in vulputate velit esse molestie consequat, vel illum dolore eu feugiat nulla facilisis at vero eros et accumsan et iusto odio dignissim qui blandit praesent luptatum zzril delenit augue duis dolore te feugait nulla Lorem ipsum dolor sit amet, consectetuer adipiscing elit, sed diam nonummy nibh euismod tincidunt ut laoreet dolore magna aliquam erat volutpat. Ut wisi enim ad minim veniam, quis nostrud exerci tation ullamcorper suscipit lobortis nisl ut aliquip ex ea commodo consequat. Duis autem vel eum iriure dolor in hendrerit in vulputate velit esse molestie consequat, vel illum dolore eu feugiat nulla facilisis at vero eros et accumsan et iusto odio dignissim qui blandit praesent luptatum zzril delenit augue duis dolore te feugait nullai.</p>
</section>

<article class="abs card" style="left:252px">
  <div class="photo" role="img" aria-label="Photo of a data center aisle with server racks" style="background:linear-gradient(90deg,#222,#777 45%,#ddd 50%,#777 55%,#222)"></div>
  <h3>Managed <span>IT Services</span></h3>
  <ul><li>Migrations &amp; Upgrades to the 9's</li><li>Report Development</li><li>Custom Applications Development</li><li>Technical and CNC</li></ul>
  <div class="more">Read <span>More</span></div>
</article>
<article class="abs card" style="left:488px">
  <div class="photo" role="img" aria-label="Photo of a blue globe beside server racks" style="background:linear-gradient(90deg,#fff,#2a7fd0 10%,#1a5faa 40%,#333 45%,#666 70%,#222)"></div>
  <h3>IT Consulting <span>Services</span></h3>
  <ul><li>Orvane Software and Technology Reseller</li><li>Ongoing Consultation</li><li>Consulting Services for World</li><li>Software Integration</li></ul>
  <div class="more">Read <span>More</span></div>
</article>

<form class="abs quick">
  <h3>Quick <span>Contact</span></h3>
  <div class="field">Name:</div>
  <div class="field">Company:</div>
  <div class="field">E-mail:</div>
  <div class="field">Phone:</div>
  <div class="field">Areas of Interest:<svg width="10" height="10"><rect width="10" height="10" fill="#ddd" stroke="#888"/><path d="M2 3h6L5 7z" fill="#333"/></svg></div>
  <div class="field area">Comments:</div>
  <div class="btns">
    <div class="btn">Submit <i><svg width="11" height="9"><path d="M1 5l3 3 6-7" fill="none" stroke="#fff" stroke-width="2"/></svg></i></div>
    <div class="btn clear">Clear <i><svg width="11" height="9"><path d="M1 5l3 3 6-7" fill="none" stroke="#fff" stroke-width="2"/></svg></i></div>
  </div>
</form>

<section class="abs partners">
  <span class="partner">Veltrix</span>
  <span class="partner blue">Harbon</span>
  <span class="partner blue">Ordexa</span>
  <span class="partner">Calvane</span>
  <span class="partner blue">Nuvora</span>
  <span class="partner">Pellix</span>
</section>
<div class="abs slide" style="left:246px;top:950px"><svg width="8" height="10"><path d="M6 1L2 5l4 4" fill="none" stroke="#fff" stroke-width="2"/></svg></div>
<div class="abs slide" style="left:927px;top:950px"><svg width="8" height="10"><path d="M2 1l4 4-4 4" fill="none" stroke="#fff" stroke-width="2"/></svg></div>

<footer class="abs footer">
  <h4 style="left:243px;top:30px">Quick Links</h4>
  <ul class="flinks" style="left:246px;top:50px"><li>Company</li><li>Products</li><li>LEDGRA</li><li>Services</li><li>Clientele</li></ul>
  <ul class="flinks" style="left:355px;top:50px"><li>Careers</li><li>Infobin</li><li>Enquiry</li><li>Sitemap</li><li>Contact</li></ul>
  <div class="vline" style="left:465px"></div>
  <h4 style="left:493px;top:30px">Support Center</h4>
  <ul class="flinks" style="left:496px;top:50px"><li style="width:95px">Free Assessment</li><li style="width:95px">Client Portal Login</li><li style="width:95px">Laecieas Deugtrat</li><li style="width:95px">Maecieas feiogtrat</li><li style="width:95px">Free Assessment</li></ul>
  <div class="vline" style="left:621px"></div>
  <h4 style="left:643px;top:29px">Connect with Us</h4>
  <div class="social" style="top:56px">Linkora <i></i></div>
  <div style="position:absolute;left:644px;top:80px;width:82px;border-top:1px dotted #777"></div>
  <div class="social" style="top:101px">Chatterly <i></i></div>
  <div class="vline" style="left:756px"></div>
  <div class="fbrand"><div class="mark"></div><div class="name">TADURK<br>INFORMATION<br>SYSTEMS PTE LTD</div></div>
  <div class="subscribe">Subscribe with Us</div>
  <div class="sub-row"><div class="in">email address</div><div class="go">Subscribe</div></div>
</footer>
<div class="abs copyright">© Copyrights 2013. Tadurk Information Systems. All Rights Reserved.</div>
</body>
</html>
```